Webdesign für HALDEN STAHLWERK
Zielgruppe
Valkorin ist Ihr leistungsstarker und zuverlässiger Partner im Bereich Metallverarbeitung. Seit unserer Firmengründung im Jahr 2001 ist unser inhabergeführtes Unternehmen in Gornau bei Chemnitz kontinuierlich gewachsen und beschäftigt derzeit 20 engagierte und qualifizierte Mitarbeiter.
Mit der Einweihung unserer neuen Fertigungshalle 2010 haben wir unsere Produktionsfläche auf 1.400 m2 vergrößert und können Ihnen nun einen noch umfassenderen Service anbieten.
Von der CNC-gesteuerten Teilefertigung bis zu modernsten Schweiß-, Schneid-, und Bearbeitungsanlagen – für die Realisierung Ihrer individuellen Wünsche steht uns ein innovativer Maschinenpark zur Verfügung. Wir fertigen zuverlässig und termingerecht nach Ihren Plänen oder übernehmen bei Bedarf auch die gesamte Abwicklung Ihres Projektes – alles made in germany!
Das Unternehmen spricht ausschließlich B2B Kunden an.
Die Hauptleistungsbereiche sind:
- Stahl- und Palettenbau
- Blechbearbeitung
- Edelstahlbearbeitung
- Mechanische Fertigung
Aufgabenstellung
- Mitlaufende Kontaktleiste
- Integration der Social Media Kanäle
- Sehr modernes Auftreten
- Industrielles Design
- Verlinkung zum Partnerunternehmen https://www.valkorin-beispiel.de/ias/index.html

```html
<!DOCTYPE html>
<html lang="de">
<head>
<meta charset="utf-8">
<title>HALDEN STAHLWERK – Valkorin Metallverarbeitung</title>
<link href="https://fonts.googleapis.com/css2?family=Manrope:wght@400;500;600;700;800&display=swap" rel="stylesheet">
<style>
:root{
  --blue:#3d8fe6;
  --navy:#111a44;
  --royal:#0b3c8c;
  --footer:#0f1731;
  --ink:#15182a;
  --muted:#8a8f9c;
  --grey:#efefef;
  --line:#e2e4ea;
}
*{margin:0;padding:0;box-sizing:border-box}
html,body{width:1200px;height:4418px;overflow:hidden;background:#fff}
body{font-family:'Manrope',sans-serif;color:var(--ink);position:relative}
.abs{position:absolute}
a{color:inherit;text-decoration:none}
.topbar{top:0;left:0;width:1200px;height:30px;background:#f3f3f3;font-size:9px;letter-spacing:.08em;color:#444;display:flex;align-items:center;padding:0 40px;gap:40px}
.topbar .social{margin-left:auto;display:flex;gap:16px}
.dot{width:10px;height:10px;border-radius:50%;background:#9aa0ad;display:inline-block}
.header{top:30px;left:0;width:1200px;height:75px;display:flex;align-items:center;padding:0 40px}
.brand{font-weight:800;font-size:30px;letter-spacing:-.02em;color:var(--ink)}
.nav{margin-left:auto;display:flex;gap:30px;font-size:12px;font-weight:600}
.nav-sep{width:1px;height:30px;background:var(--line);margin:0 32px}
.btn-outline{border:1px solid var(--blue);color:var(--blue);font-size:11px;padding:11px 18px;display:inline-flex;gap:8px;align-items:center}
.hero{top:105px;left:0;width:1200px;height:493px;background:radial-gradient(ellipse at 50% 40%,#6b5a4a 0%,#3a3431 45%,#1e1d21 100%);clip-path:polygon(0 0,100% 0,100% 400px,1131px 100%,0 100%)}
.hero h1{position:absolute;top:155px;width:100%;text-align:center;color:#fff;font-size:37px;font-weight:600;line-height:1.18}
.hero .ctas{position:absolute;top:260px;width:100%;display:flex;justify-content:center;gap:20px}
.btn-white{background:#fff;color:var(--ink);font-size:11px;padding:12px 20px;display:inline-flex;gap:8px;align-items:center}
.btn-ghost{border:1px solid #fff;color:#fff;font-size:11px;padding:12px 20px;display:inline-flex;gap:8px;align-items:center}
.hero .frame{position:absolute;left:38px;top:0;bottom:30px;width:1px;background:rgba(255,255,255,.25)}
.hero .vtext{position:absolute;left:1103px;top:110px;writing-mode:vertical-rl;transform:rotate(180deg);color:#fff;font-size:9px;letter-spacing:.14em;font-weight:600}
.sidebar{top:266px;left:1148px;width:52px}
.sidebar div{height:52px;background:var(--blue);margin-bottom:4px;display:flex;align-items:center;justify-content:center}
.eyebrow{font-size:9px;letter-spacing:.16em;color:var(--blue);font-weight:600;text-transform:uppercase}
.title{font-size:24px;font-weight:700;color:var(--ink)}
.hline{height:1px;background:var(--line)}
.grey-a{top:940px;left:0;width:957px;height:311px;background:var(--grey)}
.card{top:790px;width:211px;height:283px}
.card .ph{position:absolute;left:0;top:0;width:211px;height:252px;clip-path:polygon(0 0,186px 0,100% 25px,100% 100%,0 100%)}
.card .lbl{position:absolute;left:0;top:226px;width:155px;height:57px;background:var(--navy);color:#fff;font-size:11px;letter-spacing:.14em;font-weight:600;padding:14px 15px;line-height:1.35}
.center-btn{border:1px solid var(--navy);color:var(--navy);font-size:11px;font-weight:600;height:38px;display:flex;align-items:center;justify-content:center;gap:8px;background:#fff}
.grey-b{top:1251px;left:0;width:151px;height:490px;background:var(--grey)}
.grey-c{top:1615px;left:151px;width:254px;height:125px;background:var(--grey);clip-path:polygon(0 0,100% 0,100% 20%,110px 100%,0 100%)}
.quality-ph{top:1255px;left:151px;width:1049px;height:360px;background:linear-gradient(100deg,#c9d3df 0%,#8896a6 45%,#2b3240 70%,#9aa6b3 100%)}
.quality-box{top:1615px;left:405px;width:795px;height:248px;background:var(--navy);color:#fff}
.quality-box .eyebrow{position:absolute;left:60px;top:42px}
.quality-box h2{position:absolute;left:60px;top:58px;font-size:24px;font-weight:600;line-height:1.4;width:320px}
.quality-box .txt{position:absolute;left:385px;top:40px;width:335px;font-size:10px;line-height:1.7;color:#c9cde0}
.stat{top:2095px;text-align:center;width:228px}
.stat b{display:block;font-size:56px;font-weight:500;color:var(--blue);letter-spacing:-.02em;line-height:1}
.stat span{display:block;margin-top:16px;font-size:9px;letter-spacing:.16em;font-weight:700}
.vsep{top:2105px;width:1px;height:75px;background:var(--line)}
.arrow-btn{top:2321px;width:40px;height:38px;display:flex;align-items:center;justify-content:center}
.news{top:2396px;width:286px}
.news .ph{height:209px;clip-path:polygon(0 0,262px 0,100% 24px,100% 100%,0 100%)}
.news .tag{display:inline-block;margin-top:18px;background:var(--blue);color:#fff;font-size:8px;padding:5px 10px;border-radius:12px}
.news h3{margin-top:14px;font-size:12px;font-weight:700;letter-spacing:.02em}
.news p{margin-top:8px;font-size:8px;color:var(--muted)}
.partner-text{top:3040px;left:151px;width:510px;font-size:10px;line-height:1.7;color:var(--royal)}
.partner-logo{top:3018px;left:790px;display:flex;align-items:center;gap:12px}
.partner-logo .sq{width:42px;height:42px;background:var(--royal)}
.partner-logo b{font-size:17px;font-weight:700;color:var(--royal);line-height:1.15;letter-spacing:.02em}
.dark-base{top:3591px;left:0;width:1200px;height:734px;background:var(--footer)}
.contact-blue{top:3219px;left:151px;width:1049px;height:372px;background:var(--royal)}
.contact-dark{top:3591px;left:591px;width:609px;height:177px;background:#101d4d}
.contact-ph{top:3317px;left:0;width:591px;height:505px;background:linear-gradient(135deg,#d8dde3 0%,#9aa3ae 40%,#3a4660 75%,#1e2740 100%);clip-path:polygon(0 0,555px 0,100% 36px,100% 100%,0 100%)}
.contact-info{left:667px;color:#fff}
.contact-row{left:667px;width:380px;display:flex;gap:14px;align-items:flex-start;color:#fff}
.contact-row b{font-size:15px;font-weight:600;display:block}
.contact-row small{font-size:8px;color:var(--blue);letter-spacing:.06em;display:block;margin-top:4px}
.btn-line-white{border:1px solid #fff;color:#fff;font-size:11px;height:38px;display:flex;align-items:center;justify-content:center;gap:8px}
.footer{color:#fff}
.fhead{font-size:9px;letter-spacing:.16em;color:var(--blue);font-weight:700}
.flinks{font-size:10px;line-height:28px;color:#e2e5ee}
.fsmall{font-size:10px;line-height:1.7;color:#aeb3c5}
.btn-pill{border:1px solid #fff;border-radius:20px;font-size:11px;font-weight:600;width:82px;height:34px;display:flex;align-items:center;justify-content:center;color:#fff}
.fsocial{display:flex;gap:22px}
.fsocial i{width:16px;height:16px;border-radius:50%;background:var(--blue);display:block}
</style>
</head>
<body>

<div class="abs topbar">
  <span>T: +49 3810 / 442 716 3</span>
  <span>E: INFO@VALKORIN-BEISPIEL.DE</span>
  <div class="social"><i class="dot"></i><i class="dot"></i><i class="dot"></i><i class="dot"></i><i class="dot"></i><i class="dot"></i></div>
</div>

<header class="abs header">
  <div class="brand">VALKORIN</div>
  <nav class="nav"><a>Home</a><a>Leistungen</a><a>Produkte</a><a>Fertigung</a><a>Qualifikation</a><a>Über Uns</a></nav>
  <div class="nav-sep"></div>
  <a class="btn-outline">Kontakt <svg width="14" height="8" viewBox="0 0 14 8"><path d="M0 4h13M9.5 0.5L13 4 9.5 7.5" stroke="currentColor" fill="none"/></svg></a>
</header>

<section class="abs hero" role="img" aria-label="CNC-Fräsmaschine bearbeitet ein Metallwerkstück mit Funkenflug">
  <div class="frame"></div>
  <h1>Ihr zuverlässiger Partner im<br>Bereich der Metallverarbeitung</h1>
  <div class="ctas">
    <a class="btn-white">Angebot einholen <svg width="14" height="8" viewBox="0 0 14 8"><path d="M0 4h13M9.5 0.5L13 4 9.5 7.5" stroke="currentColor" fill="none"/></svg></a>
    <a class="btn-ghost">Jetzt mehr erfahren <svg width="14" height="8" viewBox="0 0 14 8"><path d="M0 4h13M9.5 0.5L13 4 9.5 7.5" stroke="currentColor" fill="none"/></svg></a>
  </div>
  <div class="vtext">YOUR PARTNER OF EXCELLENCE IN METALWORK</div>
</section>

<div class="abs sidebar">
  <div><svg width="18" height="18" viewBox="0 0 24 24" fill="none" stroke="#fff" stroke-width="1.6"><path d="M22 2L11 13M22 2l-7 20-4-9-9-4z"/></svg></div>
  <div><svg width="18" height="18" viewBox="0 0 24 24" fill="none" stroke="#fff" stroke-width="1.6"><path d="M22 16.9v3a2 2 0 0 1-2.2 2 19.8 19.8 0 0 1-8.6-3.1 19.5 19.5 0 0 1-6-6A19.8 19.8 0 0 1 2.1 4.2 2 2 0 0 1 4.1 2h3a2 2 0 0 1 2 1.7c.1 1 .4 1.9.7 2.8a2 2 0 0 1-.5 2.1L8 9.9a16 16 0 0 0 6 6l1.3-1.3a2 2 0 0 1 2.1-.4c.9.3 1.8.6 2.8.7a2 2 0 0 1 1.7 2z"/></svg></div>
  <div><svg width="18" height="18" viewBox="0 0 24 24" fill="none" stroke="#fff" stroke-width="1.6"><path d="M3 21h18M5 21V10h14v11M9 21v-6h6v6M4 10l8-6 8 6"/></svg></div>
</div>

<div class="abs grey-a"></div>
<div class="abs eyebrow" style="top:700px;left:151px">Leistungen</div>
<h2 class="abs title" style="top:718px;left:151px">Unsere Leistungsbereiche</h2>
<div class="abs hline" style="top:734px;left:509px;width:531px"></div>

<div class="abs card" style="left:151px"><div class="ph" role="img" aria-label="Laserschneiden von Stahlplatten" style="background:linear-gradient(160deg,#3a3d44,#6b5a4a 60%,#1f2128)"></div><div class="lbl">STAHL- UND<br>PALETTENBAU</div></div>
<div class="abs card" style="left:381px"><div class="ph" role="img" aria-label="Laserschneidkopf über Blech mit Funken" style="background:linear-gradient(160deg,#2a2230,#a5433a 55%,#3a2a35)"></div><div class="lbl">BLECH-<br>BEARBEITUNG</div></div>
<div class="abs card" style="left:610px"><div class="ph" role="img" aria-label="Mitarbeiter mit Helm zwischen Edelstahlrohren" style="background:linear-gradient(160deg,#d9dde2,#9ba4ad 60%,#5a6b86)"></div><div class="lbl">EDELSTAHL-<br>BEARBEITUNG</div></div>
<div class="abs card" style="left:840px"><div class="ph" role="img" aria-label="Facharbeiter mit Schutzbrille an der Maschine" style="background:linear-gradient(160deg,#c9ced4,#6e7684 55%,#2d3546)"></div><div class="lbl">MECHANISCHE<br>FERTIGUNG</div></div>

<a class="abs center-btn" style="top:1114px;left:490px;width:182px">Alle Leistungen ansehen <svg width="14" height="8" viewBox="0 0 14 8"><path d="M0 4h13M9.5 0.5L13 4 9.5 7.5" stroke="currentColor" fill="none"/></svg></a>

<div class="abs grey-b"></div>
<div class="abs grey-c"></div>
<div class="abs quality-ph" role="img" aria-label="Mitarbeiter richtet Werkzeug in einer CNC-Maschine ein"></div>
<section class="abs quality-box">
  <div class="eyebrow">Ihr zuverlässiger Partner</div>
  <h2>Wir vereinen Qualität und Kundenzufriedenheit</h2>
  <div class="txt">
    <p>Lorem ipsum dolor sit amet consectetur. Risus risus dui commodo posuere aenean ac mauris sed. Morbi aliquam tincidunt nibh leo. Quam ipsum sapien mauris pharetra id convallis ac nunc venenatis. Blandit viverra nunc enim sagittis accumsan habitant. Leo elit tellus sapien arcu congue sit malesuada id.</p>
    <p style="margin-top:14px">Vestibulum augue tempus sed scelerisque at tellus. Diam magna commodo donec odio. Quisque eget ridiculus risus placerat fringilla congue sit dolor. Penatibus massa urna egestas velit in tortor nec molestie tincidunt.</p>
  </div>
</section>

<div class="abs eyebrow" style="top:1989px;left:151px">Fakten und Zahlen</div>
<h2 class="abs title" style="top:2007px;left:151px">VALKORIN in Zahlen</h2>
<div class="abs stat" style="left:135px"><b>22</b><span>JAHRE EXPERTISE</span></div>
<div class="abs vsep" style="left:351px"></div>
<div class="abs stat" style="left:351px"><b>1.400</b><span>M² PRODUKTIONSFLÄCHE</span></div>
<div class="abs vsep" style="left:579px"></div>
<div class="abs stat" style="left:580px"><b>20</b><span>ENGAGIERTE MITARBEITER</span></div>
<div class="abs vsep" style="left:809px"></div>
<div class="abs stat" style="left:829px"><b>100%</b><span>MADE IN GERMANY</span></div>

<div class="abs eyebrow" style="top:2307px;left:151px">Neuigkeiten rund um die Metallverarbeitung</div>
<h2 class="abs title" style="top:2325px;left:151px">Aktuelles &amp; Neuigkeiten</h2>
<div class="abs hline" style="top:2340px;left:472px;width:456px"></div>
<div class="abs arrow-btn" style="left:960px;border:1px solid var(--line)"><svg width="14" height="8" viewBox="0 0 14 8"><path d="M14 4H1M4.5 0.5L1 4l3.5 3.5" stroke="#b7bcc6" fill="none"/></svg></div>
<div class="abs arrow-btn" style="left:1008px;background:#eceef2"><svg width="14" height="8" viewBox="0 0 14 8"><path d="M0 4h13M9.5 0.5L13 4 9.5 7.5" stroke="#555" fill="none"/></svg></div>

<article class="abs news" style="left:151px"><div class="ph" role="img" aria-label="Laserschneidanlage im Betrieb" style="background:linear-gradient(160deg,#2d3038,#7a5b45 55%,#202228)"></div><span class="tag">Categorytag</span><h3>LOREM IPSUM DOLOR SIT AMET</h3><p>vom 24. September 2023</p></article>
<article class="abs news" style="left:456px"><div class="ph" role="img" aria-label="Geschwungene Metalllamellen" style="background:linear-gradient(120deg,#3d4048,#c9ccd2 50%,#5c6068)"></div><span class="tag">Categorytag</span><h3>LOREM IPSUM DOLOR SIT AMET</h3><p>vom 24. September 2023</p></article>
<article class="abs news" style="left:761px"><div class="ph" role="img" aria-label="Metallfassade mit gefalteten Paneelen" style="background:linear-gradient(120deg,#7b8794,#cfd6de 50%,#8c97a4)"></div><span class="tag">Categorytag</span><h3>LOREM IPSUM DOLOR SIT AMET</h3><p>vom 24. September 2023</p></article>

<a class="abs center-btn" style="top:2732px;left:512px;width:153px">Alle News ansehen <svg width="14" height="8" viewBox="0 0 14 8"><path d="M0 4h13M9.5 0.5L13 4 9.5 7.5" stroke="currentColor" fill="none"/></svg></a>

<div class="abs hline" style="top:2905px;left:151px;width:889px"></div>

<div class="abs eyebrow" style="top:2970px;left:151px">Partnerunternehmen</div>
<h2 class="abs title" style="top:2987px;left:151px">Industrie- und Anlagenservice</h2>
<p class="abs partner-text">Lorem ipsum dolor sit amet consectetur. Risus risus dui commodo posuere aenean ac mauris sed. Morbi aliquam tincidunt nibh leo. Quam ipsum sapien mauris pharetra id convallis ac nunc venenatis. Blandit viverra nunc enim sagittis accumsan habitant. Leo elit tellus sapien arcu congue sit malesuada id.</p>
<a class="abs partner-logo" href="https://www.valkorin-beispiel.de/nordhag/index.html"><span class="sq"></span><b>NORDHAG<br>ANLAGENSERVICE</b></a>

<div class="abs dark-base"></div>
<div class="abs contact-blue"></div>
<div class="abs contact-dark"></div>
<div class="abs contact-ph" role="img" aria-label="Techniker mit Schutzhelm an einem Maschinenbedienpult"></div>

<h2 class="abs contact-info" style="top:3320px;font-size:24px;font-weight:600">Kontakt</h2>
<p class="abs contact-info" style="top:3355px;font-size:10px;color:#c7d2ec">So erreichen Sie uns</p>
<div class="abs contact-row" style="top:3422px"><svg width="20" height="20" viewBox="0 0 24 24" fill="none" stroke="#fff" stroke-width="1.4"><path d="M22 16.9v3a2 2 0 0 1-2.2 2 19.8 19.8 0 0 1-8.6-3.1 19.5 19.5 0 0 1-6-6A19.8 19.8 0 0 1 2.1 4.2 2 2 0 0 1 4.1 2h3a2 2 0 0 1 2 1.7c.1 1 .4 1.9.7 2.8a2 2 0 0 1-.5 2.1L8 9.9a16 16 0 0 0 6 6l1.3-1.3a2 2 0 0 1 2.1-.4c.9.3 1.8.6 2.8.7a2 2 0 0 1 1.7 2z"/></svg><div><b>+49 3810 / 442 716 00</b><small>MO–FR · 08:00 – 18:00</small></div></div>
<div class="abs hline" style="top:3471px;left:667px;width:380px;background:rgba(255,255,255,.2)"></div>
<div class="abs contact-row" style="top:3489px"><svg width="20" height="20" viewBox="0 0 24 24" fill="none" stroke="#fff" stroke-width="1.4"><path d="M22 2L11 13M22 2l-7 20-4-9-9-4z"/></svg><div><b>info@valkorin-beispiel.de</b><small style="letter-spacing:0">Wir antworten meist binnen 24 Stunden</small></div></div>
<div class="abs hline" style="top:3541px;left:667px;width:380px;background:rgba(255,255,255,.2)"></div>

<p class="abs" style="top:3640px;left:667px;font-size:11px;color:#fff;line-height:1.45">Oder nutzen Sie<br>unser <b>Kontaktformular</b></p>
<a class="abs btn-line-white" style="top:3636px;left:881px;width:166px">Zum Kontaktformular <svg width="14" height="8" viewBox="0 0 14 8"><path d="M0 4h13M9.5 0.5L13 4 9.5 7.5" stroke="currentColor" fill="none"/></svg></a>

<footer class="footer">
  <div class="abs brand" style="top:3945px;left:151px;color:#fff">VALKORIN</div>
  <p class="abs" style="top:4010px;left:151px;font-size:10px;font-weight:700">Valkorin GmbH</p>
  <p class="abs fsmall" style="top:4028px;left:151px">Musterstraße 1<br>12345 Musterstadt<br>Deutschland</p>
  <p class="abs fsmall" style="top:4092px;left:151px;width:265px">Lorem ipsum dolor sit amet consectetur. Dolor cras eget a volutpat ullamcorper facilisis. Viverra aliquam ac aliquet aliquet odio in aliquet.</p>

  <div class="abs fhead" style="top:3944px;left:454px">SEITEN</div>
  <div class="abs flinks" style="top:3962px;left:454px">Leistungen<br>Produkte<br>Fertigung<br>Qualifikation<br>Über uns</div>

  <div class="abs fhead" style="top:3944px;left:608px">RECHTLICHES</div>
  <div class="abs flinks" style="top:3962px;left:608px">Impressum<br>Datenschutzerklärung</div>
  <div class="abs fhead" style="top:4052px;left:608px">KONTAKT &amp; SONSTIGES</div>
  <div class="abs flinks" style="top:4070px;left:608px">FAQ<br>Kontakt<br>Links</div>

  <div class="abs fhead" style="top:3944px;left:838px">KONTAKTINFORMATIONEN</div>
  <p class="abs" style="top:3984px;left:838px;font-size:10px;line-height:1.5">Telefon:<br><span style="color:var(--blue);font-weight:600">+49 3810 / 442 716 00</span></p>
  <p class="abs" style="top:4034px;left:838px;font-size:10px;line-height:1.5">E-MAIL:<br><span style="color:var(--blue);font-weight:600;text-decoration:underline">info@valkorin-beispiel.de</span></p>
  <a class="abs btn-pill" style="top:4078px;left:838px">Kontakt</a>

  <p class="abs" style="top:4222px;left:151px;font-size:10px">Copyright © 2023 valkorin-beispiel.de</p>
  <div class="abs fsocial" style="top:4220px;left:843px"><i></i><i></i><i></i><i></i><i></i><i></i></div>
</footer>

</body>
</html>
```